Business Cards for new orthopaedic surgery practice

My husband and I are starting our own orthopaedic surgery practice. We are looking for a business card that is uniform, but one will have my name/title and the other will have his. You can just create one design with my name on it for now. But when I choose your design as the winning design I will ask that you add another copy with his name/title.

We are looking for classy, simple, elite all in one. We like dark blues/a little gold/yellow. Something that goes with our logo. We want our logo incorporated. Here is all the info you need:
Business name: RV Bone & Vitality Center
Location: 38517 North Willowmere Ave
Harbor Pines, FL 33999
Phone: 954-218-4063
Fax: 954-582-7341
Email: info@myrvbonecare.example

Names: Lydia Vance, M.D.
Board Certified Hand and Upper Extremity Surgeon

Ebo Dansu, M.D.
Board Certified Hip & Knee Replacement/General Orthopaedic Surgeon

Can decide what you want to put on the back. Maybe a slogan:
Rooted in Care. Focused on You

I am just going to upload our logo. The only thing is if we select you as the winning design, the location, and phone numbers may change. We will need your help to update that once fully solidified.

Industry/Entity Type

Medical

Contact Information for Business Card

Colors
0054AA
0677BA
7BADD7
CADEEF
E8F1F8
0094D4
00A9DD
6FCCEA
C7EBF8
E9F6FB

Requirements
Must have
• class, appeal,
Should not have
• We want to air on the side of masculine if we are looking at masculine vs. feminine feel. But we still want it classy, sophisticated, and something we will love

```html
<!DOCTYPE html>
<html lang="en">
<head>
<meta charset="utf-8">
<title>RV Bone &amp; Vitality Center – Business Card</title>
<link rel="stylesheet" href="https://fonts.googleapis.com/css2?family=Outfit:wght@400;600&display=swap">
<style>
  :root {
    --navy: #0c2c6e;
    --cyan: #1fb3e0;
    --white: #ffffff;
    --backdrop: #9a9a9a;
  }
  * { margin: 0; padding: 0; box-sizing: border-box; }
  html, body { width: 1200px; height: 1200px; overflow: hidden; }
  body {
    position: relative;
    background: var(--backdrop);
    font-family: "Outfit", sans-serif;
  }
  .card {
    position: absolute;
    left: 281px;
    width: 649px;
    height: 370px;
    border-radius: 40px;
    overflow: hidden;
  }
  .card-front {
    top: 166px;
    background: var(--navy);
    display: flex;
    align-items: center;
    justify-content: center;
  }
  .brand-name {
    color: var(--white);
    font-weight: 600;
    font-size: 36px;
    letter-spacing: 0.5px;
  }
  .card-back {
    top: 615px;
    background: var(--navy);
  }
  .brand-panel {
    position: absolute;
    left: 0; top: 0;
    width: 201px; height: 100%;
    background: var(--white);
  }
  .brand-panel .brand-vertical {
    position: absolute;
    left: 50%; top: 50%;
    transform: translate(-50%, -50%) rotate(-90deg);
    white-space: nowrap;
    color: var(--navy);
    font-weight: 600;
    font-size: 22px;
  }
  .holder {
    position: absolute;
    left: 278px;
    top: 54px;
  }
  .holder-name {
    color: var(--cyan);
    font-weight: 600;
    font-size: 22px;
    letter-spacing: 0.2px;
  }
  .holder-title {
    margin-top: 6px;
    color: var(--white);
    font-size: 15px;
    line-height: 20px;
  }
  .contact-list {
    position: absolute;
    left: 279px;
    top: 168px;
    list-style: none;
  }
  .contact-item {
    display: flex;
    align-items: flex-start;
    color: var(--white);
    font-size: 15px;
    line-height: 20px;
    height: 32px;
  }
  .contact-icon {
    flex: none;
    width: 25px; height: 25px;
    margin-right: 10px;
    margin-top: -2px;
    border: 1.5px solid var(--cyan);
    border-radius: 2px;
    display: flex;
    align-items: center;
    justify-content: center;
  }
  .contact-icon svg { width: 13px; height: 13px; }
</style>
</head>
<body>
  <section class="card card-front">
    <span class="brand-name">RV Bone &amp; Vitality Center</span>
  </section>

  <section class="card card-back">
    <div class="brand-panel">
      <span class="brand-vertical">RV Bone &amp; Vitality Center</span>
    </div>

    <div class="holder">
      <h1 class="holder-name">LYDIA VANCE, M.D.</h1>
      <p class="holder-title">Board Certified Hand and<br>Upper Extremity Surgeon</p>
    </div>

    <ul class="contact-list">
      <li class="contact-item">
        <span class="contact-icon">
          <svg viewBox="0 0 24 24" fill="#1fb3e0"><path d="M6.6 10.8a15.1 15.1 0 0 0 6.6 6.6l2.2-2.2c.3-.3.7-.4 1-.2 1.1.4 2.3.6 3.6.6.6 0 1 .4 1 1V20c0 .6-.4 1-1 1C10.6 21 3 13.4 3 4c0-.6.4-1 1-1h3.5c.6 0 1 .4 1 1 0 1.3.2 2.5.6 3.6.1.3 0 .7-.2 1z"/></svg>
        </span>954-218-4063
      </li>
      <li class="contact-item">
        <span class="contact-icon">
          <svg viewBox="0 0 24 24" fill="none" stroke="#1fb3e0" stroke-width="2"><rect x="7" y="3" width="10" height="6"/><rect x="3" y="9" width="18" height="8" rx="1"/><rect x="7" y="14" width="10" height="7"/></svg>
        </span>954-582-7341
      </li>
      <li class="contact-item">
        <span class="contact-icon">
          <svg viewBox="0 0 24 24" fill="#1fb3e0"><path d="M2 5h20v14H2z"/><path d="M2 5l10 8 10-8" fill="none" stroke="#0c2c6e" stroke-width="2"/></svg>
        </span>info@myrvbonecare.example
      </li>
      <li class="contact-item">
        <span class="contact-icon">
          <svg viewBox="0 0 24 24" fill="none" stroke="#1fb3e0" stroke-width="2.4"><path d="M12 22s7-7 7-12a7 7 0 0 0-14 0c0 5 7 12 7 12z"/><circle cx="12" cy="10" r="2.5"/></svg>
        </span>38517 North Willowmere Ave<br>Harbor Pines, FL 33999
      </li>
    </ul>
  </section>
</body>
</html>
```